Velmora Consulting Business

** Please add the content information from my old business card
1. I would like to see a two sided business card with both options with the 1st Option--Tallow Spire-new WHITE BACKGROUND LOGO
2 nd Option-Tallow Spire - new BLACK- Background Logo
3rd -Option a business card with my Photo on the card
Please add the new word to the card information:
EXECUTION
AS THE OWNER'S REP
WE AIM TO ACHIEVE YOUR
INFRASTRUCTURE VISION with
OUR SPECIALIZATION & EXECUTION in:

FUNDING Planning
BUSINESS Planning
INFRASTRUCTURE Planning
PROJECT Management
Since 2012
_____________________________________________________________________
I want to get spot uv raised printing. I was liking a a nice rich white linen paper stock with black writing & NOT A COLORED CARD other than a variety of white or black cards concept

```html
<!DOCTYPE html>
<html lang="en">
<head>
<meta charset="utf-8">
<title>Velmora Consulting – Business Card</title>
<link rel="stylesheet" href="https://fonts.googleapis.com/css2?family=Open+Sans:wght@400;600;700;800&display=swap">
<style>
  :root {
    --stage: #232323;
    --card: #2b2b2e;
    --edge: #e3141b;
    --red: #e8141c;
    --white: #ffffff;
    --soft: #e9e9e9;
    --font: "Open Sans", Arial, sans-serif;
  }
  * { box-sizing: border-box; margin: 0; padding: 0; }
  html, body { width: 1200px; height: 780px; overflow: hidden; }
  body {
    background: var(--stage);
    font-family: var(--font);
    color: var(--white);
    display: flex;
    align-items: center;
    justify-content: center;
    gap: 40px;
  }
  .card {
    position: relative;
    width: 540px;
    height: 309px;
    background: var(--card);
    border-radius: 22px;
    border-bottom: 4px solid var(--edge);
    border-left: 2px solid var(--edge);
    overflow: hidden;
    box-shadow: 0 14px 30px rgba(0,0,0,.55);
  }

  /* Back side */
  .leaf-decoration {
    position: absolute;
    left: 30px; top: 20px;
    width: 250px; height: 270px;
    border-radius: 40% 40% 30% 30%;
    background: linear-gradient(180deg, #555558 0%, #18181a 55%, #0c0c0d 100%);
    opacity: .9;
  }
  .brand {
    position: absolute;
    font-weight: 700;
    color: var(--white);
    line-height: 1.1;
    display: flex;
    align-items: center;
    gap: 8px;
  }
  .brand-dot { width: 10px; height: 10px; border-radius: 50%; background: var(--red); flex: none; }
  .card-back .brand { left: 60px; top: 122px; width: 200px; font-size: 26px; }
  .mission {
    position: absolute;
    left: 300px; top: 62px;
    width: 225px;
    font-size: 10.5px;
    line-height: 1.45;
    color: var(--soft);
  }
  .services {
    position: absolute;
    left: 330px; top: 150px;
    list-style: none;
    font-size: 12px;
    line-height: 1.35;
  }
  .services b { font-weight: 800; }
  .services .accent { color: var(--red); }

  /* Front side */
  .red-tab {
    position: absolute; right: 0; top: 16px;
    width: 22px; height: 46px;
    background: var(--red);
  }
  .person {
    position: absolute;
    right: 30px; top: 20px;
    text-align: right;
  }
  .person-name { color: var(--red); font-weight: 800; font-size: 24px; line-height: 1.1; }
  .person-role { font-size: 12px; letter-spacing: .3px; text-transform: uppercase; margin-top: 3px; }
  .portrait {
    position: absolute;
    right: 0; bottom: 0;
    width: 230px; height: 196px;
    border-top-left-radius: 110px 90px;
    background: radial-gradient(circle at 40% 25%, #b5744a 0%, #6b4030 22%, #141414 50%, #0d0d0d 100%);
  }
  .card-front .brand { left: 40px; top: 72px; font-size: 26px; }
  .contacts {
    position: absolute;
    left: 40px; top: 178px;
    list-style: none;
    font-size: 13px;
    line-height: 1.6;
  }
  .contacts li { display: flex; align-items: center; gap: 9px; }
  .contacts svg { width: 13px; height: 13px; flex: none; }
  .locations {
    position: absolute;
    left: 40px; bottom: 22px;
    font-size: 14px;
    display: flex; align-items: center; gap: 8px;
  }
  .locations .sep { width: 8px; height: 8px; border-radius: 50%; background: var(--red); }
</style>
</head>
<body>
  <section class="card card-back" aria-label="Card back">
    <div class="leaf-decoration" role="img" aria-label="Large dark maple leaf decoration"></div>
    <div class="brand"><span class="brand-dot"></span><span>Velmora Consulting</span></div>
    <p class="mission">AS THE OWNER'S REP<br>WE AIM TO ACHIEVE YOUR<br>INFRASTRUCTURE VISION with<br>OUR SPECIALIZATION &amp; EXECUTION in:</p>
    <ul class="services">
      <li><b>FUNDING</b> Planning</li>
      <li class="accent"><b>BUSINESS</b> Planning</li>
      <li><b>PROJECT</b> Management</li>
      <li class="accent"><b>INFRASTRUCTURE</b> Planning</li>
    </ul>
  </section>

  <section class="card card-front" aria-label="Card front">
    <div class="red-tab"></div>
    <div class="person">
      <div class="person-name">Corinne Vale-Ashford</div>
      <div class="person-role">CEO / Lead Project Manager</div>
    </div>
    <div class="portrait" role="img" aria-label="Portrait photo of the CEO"></div>
    <div class="brand"><span class="brand-dot"></span>Velmora Consulting</div>
    <ul class="contacts">
      <li>
        <svg viewBox="0 0 16 16" aria-hidden="true"><path fill="#e8141c" d="M3.5 1.5l2.5 2.7-1.3 1.6a9 9 0 0 0 5.5 5.5l1.6-1.3 2.7 2.5-1.7 2A12 12 0 0 1 1.5 3.2z"/></svg>
        867.555.0142
      </li>
      <li>
        <svg viewBox="0 0 16 16" aria-hidden="true"><circle cx="8" cy="8" r="6.5" fill="none" stroke="#e8141c" stroke-width="1.6"/><path d="M1.5 8h13M8 1.5c-3 3.5-3 9.5 0 13M8 1.5c3 3.5 3 9.5 0 13" fill="none" stroke="#e8141c" stroke-width="1.2"/></svg>
        corinne@velmora.ca
      </li>
      <li>
        <svg viewBox="0 0 16 16" aria-hidden="true"><rect x="1.5" y="3.5" width="13" height="9" rx="1" fill="none" stroke="#e8141c" stroke-width="1.6"/><path d="M1.5 4l6.5 5 6.5-5" fill="none" stroke="#e8141c" stroke-width="1.4"/></svg>
        www.velmora.ca
      </li>
    </ul>
    <div class="locations"><span>Kestrel Bay NT</span><span class="sep"></span><span>Harrow Mills NB</span></div>
  </section>
</body>
</html>
```